Tallow Peak Moves Strong Healthy

We are a fitness business
Personal training
Strength & Conditioning
Boxing
Bootcamp
Kinvex
And much more
Fitness for all levels
4/27 Marlowe Street Brindle Cove

You have designed my logo so I would like that on the business card.

```html
<!DOCTYPE html>
<html lang="en">
<head>
<meta charset="utf-8">
<title>Tallow Peak Moves – Business Card</title>
<link href="https://fonts.googleapis.com/css2?family=Arimo:wght@400;700&display=swap" rel="stylesheet">
<style>
  :root {
    --stage: #3a3a3c;
    --card: #161618;
    --card-edge: #232325;
    --brand-blue: #3a78c9;
    --text-light: #f2f2f2;
  }
  * { margin: 0; padding: 0; box-sizing: border-box; }
  html, body {
    width: 1200px; height: 900px; overflow: hidden;
    background: var(--stage);
    font-family: "Arimo", Arial, sans-serif;
  }
  .card {
    position: absolute; left: 250px;
    width: 700px; height: 400px;
    background: var(--card);
    border-radius: 22px;
    border: 1px solid var(--card-edge);
    overflow: hidden;
  }
  .card-front { top: 30px; }
  .card-back { top: 470px; }

  .brand {
    display: flex; align-items: center; gap: 14px;
    color: var(--brand-blue); font-weight: 700;
    text-transform: uppercase; letter-spacing: 1px;
    white-space: nowrap;
  }
  .brand-dot { border-radius: 50%; background: var(--brand-blue); flex: none; }

  /* front */
  .card-front .brand {
    position: absolute; top: 120px; left: 0; right: 0;
    justify-content: center; font-size: 44px;
  }
  .card-front .brand-dot { width: 44px; height: 44px; }
  .services {
    position: absolute; top: 230px; left: 0; right: 0;
    text-align: center; color: var(--text-light);
    font-size: 19px; line-height: 32px;
  }
  .services .sep { margin: 0 10px; }

  /* back */
  .card-back .brand {
    position: absolute; top: 50px; right: 50px; font-size: 30px;
  }
  .card-back .brand-dot { width: 32px; height: 32px; }
  .holder {
    position: absolute; top: 140px; left: 40px;
    padding-left: 22px; border-left: 14px solid var(--brand-blue);
  }
  .holder-name { color: var(--text-light); font-size: 28px; }
  .holder-title { color: var(--brand-blue); font-size: 19px; margin-top: 2px; }
  .contact {
    position: absolute; left: 50px; top: 240px;
    list-style: none; color: var(--text-light); font-size: 20px;
  }
  .contact li { display: flex; align-items: center; gap: 12px; height: 32px; }
  .contact svg { width: 20px; height: 20px; fill: var(--brand-blue); flex: none; }
  .baseline {
    position: absolute; left: 50px; right: 250px; bottom: 44px;
    height: 3px; background: var(--brand-blue);
  }
  .social {
    position: absolute; right: 40px; bottom: 36px;
    color: var(--text-light); font-size: 19px;
  }
</style>
</head>
<body>

<section class="card card-front">
  <div class="brand"><span class="brand-dot"></span>Tallow Peak Moves</div>
  <p class="services">
    Personal training<span class="sep">|</span>Strength &amp; Conditioning<span class="sep">|</span>Boxing<span class="sep">|</span>Bootcamp<br>
    Kinvex<span class="sep">|</span>And much more
  </p>
</section>

<section class="card card-back">
  <div class="brand"><span class="brand-dot"></span>Tallow Peak Moves</div>
  <div class="holder">
    <div class="holder-name">Your Name</div>
    <div class="holder-title">Job Title</div>
  </div>

  <ul class="contact">
    <li>
      <svg viewBox="0 0 20 20" aria-hidden="true"><path d="M2 6c0-2 2-3 8-3s8 1 8 3v2h-4V6H6v2H2z M5 9h10l2 8H3z"/></svg>
      000 000 0000
    </li>
    <li>
      <svg viewBox="0 0 20 20" aria-hidden="true"><path d="M1 4h18v12H1z M2 5l8 6 8-6" stroke="#161618" stroke-width="1.4"/></svg>
      youremail@xyz.com
    </li>
    <li>
      <svg viewBox="0 0 20 20" aria-hidden="true"><path d="M10 1a6 6 0 0 1 6 6c0 5-6 12-6 12S4 12 4 7a6 6 0 0 1 6-6zm0 3.5a2.5 2.5 0 1 0 0 5 2.5 2.5 0 0 0 0-5z"/></svg>
      4/27 Marlowe Street Brindle Cove
    </li>
  </ul>

  <div class="baseline"></div>
  <div class="social">tallowpeakmoves/</div>
</section>

</body>
</html>
```